Orvane Mechanical - Letterhead

We are a plumbing and hvac company based in Calgary. This letterhead will be on our quotes, invoices, preventative maintenance proposals etc.

```html
<!DOCTYPE html>
<html lang="en">
<head>
<meta charset="utf-8">
<title>Orvane Mechanical – Letterhead</title>
<link href="https://fonts.googleapis.com/css2?family=Open+Sans:wght@400;600;700&display=swap" rel="stylesheet">
<style>
  :root{
    --orange:#e8522a;
    --blue:#2f6fc0;
    --ink:#2b2b2b;
    --paper:#ffffff;
    --backdrop:#e3e4e5;
    --signature-tone:#dedfe1;
  }
  *{margin:0;padding:0;box-sizing:border-box}
  html,body{width:1200px;height:945px;overflow:hidden;background:var(--backdrop)}
  body{font-family:"Open Sans",sans-serif;color:var(--ink)}
  .sheet{
    position:absolute;left:260px;top:28px;width:680px;height:889px;
    background:var(--paper);box-shadow:0 6px 22px rgba(0,0,0,.12);overflow:hidden;
  }
  .header-band{position:absolute;left:0;top:0;width:680px;height:130px}
  .contact{
    position:absolute;right:90px;top:16px;list-style:none;
    font-size:9.5px;line-height:13px;color:#fff;
  }
  .contact li{display:flex;align-items:center;gap:6px}
  .contact svg{width:9px;height:9px;flex:none}
  .brand{position:absolute;left:58px;top:92px;display:flex;align-items:center;gap:8px}
  .brand-dot{width:16px;height:16px;border-radius:50%;background:var(--orange)}
  .brand-name{font-weight:700;font-size:19px;color:var(--blue);letter-spacing:.2px}
  .letter{position:absolute;left:92px;top:240px;width:500px}
  .greeting{font-weight:700;font-size:14px;margin-bottom:14px}
  .letter p{font-size:12px;line-height:15.5px;text-align:justify;margin:0 0 18px 14px}
  .signature{position:absolute;left:112px;top:640px;width:140px;height:54px;background:var(--signature-tone);border-radius:4px}
  .address{
    position:absolute;left:92px;bottom:38px;display:flex;align-items:center;gap:6px;
    font-size:11px;color:var(--ink);
  }
  .address svg{width:10px;height:13px}
</style>
</head>
<body>
  <main class="sheet">
    <svg class="header-band" viewBox="0 0 680 130" aria-hidden="true">
      <path d="M0 0H680V92C470 58 250 52 90 74C45 82 18 100 0 125Z" fill="var(--orange)"/>
      <path d="M680 92C470 58 250 52 90 74C45 82 18 100 0 125V130C20 106 48 88 92 80C250 60 470 66 680 104Z" fill="var(--blue)"/>
    </svg>

    <ul class="contact">
      <li><svg viewBox="0 0 10 10"><path d="M2 1l2 2-1 1.2c.6 1.2 1.6 2.2 2.8 2.8L7 6l2 2-1.4 1.4C4.5 9 1 5.5.6 2.4Z" fill="#fff"/></svg>855-310-2284</li>
      <li><svg viewBox="0 0 10 10"><rect x="0.5" y="2" width="9" height="6" fill="#fff"/><path d="M.5 2L5 5.5 9.5 2" stroke="var(--orange)" fill="none"/></svg>info@orvanemechanical.com</li>
      <li><svg viewBox="0 0 10 10"><circle cx="5" cy="5" r="4.3" fill="none" stroke="#fff"/><path d="M.7 5h8.6M5 .7c-2.4 2.6-2.4 6 0 8.6M5 .7c2.4 2.6 2.4 6 0 8.6" stroke="#fff" fill="none" stroke-width=".8"/></svg>www.orvanemechanical.com</li>
    </ul>

    <div class="brand">
      <span class="brand-dot"></span>
      <span class="brand-name">Orvane Mechanical</span>
    </div>

    <section class="letter">
      <h1 class="greeting">Dear Mr. John,</h1>
      <p>Lorem Ipsum is simply dummy text of the printing and typesetting industry. Lorem Ipsum has been the industry's standard dummy text ever since the 1500s, when an unknown printer took a galley of type and scrambled it to make a type specimen book. It has survived not only five centuries, but also the leap into electronic typesetting, remaining essentially unchanged.</p>
      <p>The standard chunk of Lorem Ipsum used since the 1500s is reproduced below for those interested. Sections 1.10.32 and 1.10.33 from "de Forma Verborum et Linearum" by Varelo are also reproduced in their exact original form, accompanied by English versions from the 1914 translation by J. Morrow</p>
      <p>Lorem Ipsum is simply dummy text of the printing and typesetting industry. Lorem Ipsum has been the industry's standard dummy text ever since the 1500s, when an unknown printer took a galley of type and scrambled it to make a type specimen book. It has survived not only five centuries, but also the leap into electronic typesetting, remaining essentially unchanged. It was popularised in the</p>
      <p>The standard chunk of Lorem Ipsum used since the 1500s is reproduced below for those interested. Sections 1.10.32 and 1.10.33 from "de Forma Verborum et Linearum" by Varelo are also reproduced in their exact original form, accompanied by English versions from the 1914 translation by J. Morrow</p>
    </section>

    <div class="signature" role="img" aria-label="Handwritten signature"></div>

    <footer class="address">
      <svg viewBox="0 0 10 13" aria-hidden="true"><path d="M5 0a5 5 0 0 0-5 5c0 3.5 5 8 5 8s5-4.5 5-8a5 5 0 0 0-5-5Z" fill="var(--orange)"/><circle cx="5" cy="5" r="2" fill="#fff"/></svg>
      <span>Po. Box 56, Street Name, City Name, Zip Code - 00000</span>
    </footer>
  </main>
</body>
</html>
```